I am a home builder and developer

I would like some sort of architectural design like a pencil type of drawing of a house but want it to be professional looking and two sided.

Simply I am a custom home builder and land developer. I would like a new design other than what I have now that's what I thought y'all did. I like mostly black maybe with an pencil type of drawing of a house. Like an architectural look.

Industry/Entity Type

Home Builder

```html
<!DOCTYPE html>
<html lang="en">
<head>
<meta charset="utf-8">
<title>Ridgeline Homes Inc — Business Card</title>
<link rel="stylesheet" href="https://fonts.googleapis.com/css2?family=Montserrat:wght@300;400&family=Open+Sans:wght@400;600&family=Noto+Serif:wght@400&display=swap">
<style>
  :root {
    --backdrop: #dcdadb;
    --card-dark: #2a2a2b;
    --card-light: #f4f4f4;
    --ink: #1e1e1e;
    --ink-soft: #555555;
    --accent: #b5182b;
    --paper-text: #f2f2f2;
  }
  * { margin: 0; padding: 0; box-sizing: border-box; }
  html, body {
    width: 1200px; height: 900px; overflow: hidden;
    background: var(--backdrop);
  }
  .canvas {
    width: 1200px; height: 900px;
    display: flex; flex-direction: column;
    align-items: center; justify-content: center; gap: 40px;
  }
  .card {
    width: 700px; height: 400px; position: relative;
    box-shadow: 0 6px 18px rgba(0,0,0,0.18);
  }
  /* Front side */
  .card-front {
    background: var(--card-dark);
    display: flex; flex-direction: column;
    align-items: center; justify-content: center;
  }
  .brand {
    display: flex; align-items: center; gap: 14px;
  }
  .brand-square {
    width: 22px; height: 22px; background: var(--accent);
  }
  .brand-name {
    font-family: "Open Sans", sans-serif; font-weight: 600;
    letter-spacing: 0.06em; text-transform: uppercase;
  }
  .card-front .brand-name { color: var(--paper-text); font-size: 40px; }
  .tagline {
    margin-top: 26px;
    font-family: "Open Sans", sans-serif; font-weight: 400;
    font-size: 21px; color: var(--paper-text);
  }
  /* Back side */
  .card-back { background: linear-gradient(135deg, #f7f7f7, #e9e9e9); }
  .identity {
    position: absolute; left: 44px; top: 54px;
    display: flex; gap: 14px;
  }
  .identity-bar { width: 8px; background: var(--accent); }
  .person-name {
    font-family: "Montserrat", sans-serif; font-weight: 300;
    font-size: 34px; color: var(--ink); line-height: 1.15;
  }
  .job-title {
    font-family: "Noto Serif", serif; font-size: 20px;
    color: var(--accent); margin-top: 2px;
  }
  .card-back .brand {
    position: absolute; right: 44px; top: 150px;
  }
  .card-back .brand-name { color: var(--ink); font-size: 30px; }
  .contact {
    position: absolute; left: 44px; bottom: 44px;
    list-style: none;
    font-family: "Open Sans", sans-serif; font-size: 20px; color: var(--ink-soft);
  }
  .contact li { display: flex; align-items: center; gap: 14px; margin-top: 8px; }
  .contact svg { width: 22px; height: 22px; fill: var(--accent); flex: none; }
</style>
</head>
<body>
<main class="canvas">
  <section class="card card-front" aria-label="Card front">
    <div class="brand">
      <span class="brand-square"></span>
      <span class="brand-name">Ridgeline Homes Inc</span>
    </div>
    <p class="tagline">Custom home builder and land developer</p>
  </section>

  <section class="card card-back" aria-label="Card back">
    <div class="identity">
      <span class="identity-bar"></span>
      <div>
        <p class="person-name">Daniel Corwin</p>
        <p class="job-title">Job Title</p>
      </div>
    </div>
    <div class="brand">
      <span class="brand-square"></span>
      <span class="brand-name">Ridgeline Homes Inc</span>
    </div>
    <ul class="contact">
      <li>
        <svg viewBox="0 0 24 24" aria-hidden="true"><path d="M3 8c0-2 2-3 9-3s9 1 9 3v2h-5V8H8v2H3zM6 11h12l2 9H4zm6 2a3 3 0 1 0 0 6 3 3 0 0 0 0-6z"/></svg>
        <span>555-014-2290</span>
      </li>
      <li>
        <svg viewBox="0 0 24 24" aria-hidden="true"><path d="M2 5h20v14H2zm2 2v.5l8 5.5 8-5.5V7zm0 2.9V17h16V9.9l-8 5.5z"/></svg>
        <span>hello@ridgelinehomes.example</span>
      </li>
    </ul>
  </section>
</main>
</body>
</html>
```